Carpet cleaning company focused on high quality needs business cards

We are a growing company that just merged with another company and need to design a new business card. We do both residential as well as commercial cleaning. We do carpet, tile & grout, upholstery, hard floors, and stain & pet odor removal. We treat our customers like family and strive to achieve outstanding results with every job.

```html
<!DOCTYPE html>
<html lang="en">
<head>
<meta charset="utf-8">
<title>Marlow Steam Care – Business Card</title>
<link href="https://fonts.googleapis.com/css2?family=Source+Sans+3:wght@400;600;700;900&display=swap" rel="stylesheet">
<style>
  :root {
    --page-bg: #3a3a3c;
    --card-bg: #ffffff;
    --ink: #1b1b1b;
    --text: #4a4a4a;
    --accent-blue: #1a7bbf;
    --accent-red: #e0463a;
    --divider: #e0463a;
  }
  * { margin: 0; padding: 0; box-sizing: border-box; }
  html, body {
    width: 1200px; height: 900px; overflow: hidden;
    background: var(--page-bg);
    font-family: "Source Sans 3", "Myriad Pro", sans-serif;
  }
  .sheet {
    width: 1200px; height: 900px;
    display: flex; flex-direction: column; align-items: center; justify-content: center;
    gap: 24px;
  }
  .card {
    width: 700px; height: 400px;
    background: var(--card-bg);
    border-radius: 34px;
    position: relative;
    overflow: hidden;
    box-shadow: 0 10px 28px rgba(0,0,0,.35);
  }
  .brand { display: flex; align-items: center; gap: 12px; }
  .brand-mark { width: 34px; height: 34px; background: var(--accent-red); flex: none; }
  .brand-name {
    font-weight: 900; color: var(--ink);
    font-size: 34px; line-height: 1; letter-spacing: -0.5px; white-space: nowrap;
  }

  /* front */
  .card-front {
    display: flex; flex-direction: column; align-items: center;
    padding-top: 70px; text-align: center;
  }
  .card-front .brand { margin-bottom: 30px; }
  .section-title { color: var(--accent-blue); font-weight: 600; font-size: 20px; line-height: 1.2; }
  .hours, .services-list { color: var(--text); font-size: 16.5px; line-height: 1.3; }
  .hours { margin-bottom: 12px; }
  .tagline { margin-top: 14px; color: var(--ink); font-weight: 700; font-size: 18px; }

  /* back */
  .card-back .brand { position: absolute; left: 60px; top: 120px; }
  .card-back .brand-name { font-size: 28px; }
  .card-back .brand-mark { width: 30px; height: 30px; }
  .owner { position: absolute; left: 130px; top: 230px; width: 250px; text-align: right; }
  .owner-role { color: var(--text); font-size: 17px; }
  .owner-name { color: var(--accent-blue); font-size: 19px; font-weight: 600; letter-spacing: .5px; }
  .divider {
    position: absolute; left: 405px; top: 120px; width: 1.5px; height: 170px;
    background: var(--divider);
  }
  .contact {
    position: absolute; left: 425px; top: 120px; list-style: none;
    color: var(--text); font-size: 15.5px; line-height: 1.45;
  }
  .contact li { display: flex; align-items: flex-start; gap: 8px; }
  .contact svg { width: 14px; height: 14px; margin-top: 4px; flex: none; fill: var(--accent-blue); }
  .cities { display: block; }
</style>
</head>
<body>
<main class="sheet">

  <section class="card card-front" aria-label="Business card front">
    <div class="brand">
      <span class="brand-mark"></span>
      <span class="brand-name">Marlow Steam Care</span>
    </div>
    <h2 class="section-title">Our Services Time</h2>
    <p class="hours">Mon.Tue.Wed.Thur.Fri- 9:00am - 6:00pm | Sat.Sun- Closed</p>
    <h2 class="section-title">Our Services</h2>
    <p class="services-list">
      Natural Carpets / Residential Carpet Cleaning / Tile &amp; Grout<br>
      Upholstery / Hard Floors / Dining Room And Office Chairs<br>
      Stain &amp; Pet Odor Removal
    </p>
    <p class="tagline">A Clean Like You've Never Seen</p>
  </section>

  <section class="card card-back" aria-label="Business card back">
    <div class="brand">
      <span class="brand-mark"></span>
      <span class="brand-name">Marlow Steam Care</span>
    </div>
    <div class="owner">
      <p class="owner-role">Owner</p>
      <p class="owner-name">MARLOW CARE GROUP</p>
    </div>
    <span class="divider"></span>
    <ul class="contact">
      <li>
        <svg viewBox="0 0 24 24" aria-hidden="true"><path d="M6.6 10.8a15 15 0 0 0 6.6 6.6l2.2-2.2a1 1 0 0 1 1-.25 11.4 11.4 0 0 0 3.6.57 1 1 0 0 1 1 1V20a1 1 0 0 1-1 1A17 17 0 0 1 3 4a1 1 0 0 1 1-1h3.5a1 1 0 0 1 1 1c0 1.25.2 2.45.57 3.6a1 1 0 0 1-.25 1z"/></svg>
        (555) 014-2290
      </li>
      <li>
        <svg viewBox="0 0 24 24" aria-hidden="true"><path d="M2 5h20v14H2zm2 2v.5l8 5 8-5V7l-8 5z"/></svg>
        hello@marlowsteamcare.com
      </li>
      <li>
        <svg viewBox="0 0 24 24" aria-hidden="true"><path d="M12 2a10 10 0 1 0 0 20 10 10 0 0 0 0-20zm0 2c.9 0 2.2 1.9 2.7 5H9.3C9.8 5.9 11.1 4 12 4zM4.3 11h3a16 16 0 0 0 0 2h-3a8 8 0 0 1 0-2zm5 0h5.4a14 14 0 0 1 0 2H9.3a14 14 0 0 1 0-2zm7.4 0h3a8 8 0 0 1 0 2h-3a16 16 0 0 0 0-2zM9.3 15h5.4c-.5 3.1-1.8 5-2.7 5s-2.2-1.9-2.7-5z"/></svg>
        www.marlowsteamcare.com
      </li>
      <li>
        <svg viewBox="0 0 24 24" aria-hidden="true"><path d="M12 2a7 7 0 0 0-7 7c0 5 7 13 7 13s7-8 7-13a7 7 0 0 0-7-7zm0 9.5A2.5 2.5 0 1 1 12 6.5a2.5 2.5 0 0 1 0 5z"/></svg>
        <span class="cities">
          Alderbrook, OH, US<br>
          Millhaven Falls, OH, US<br>
          Pine Hollow, OH, US<br>
          East Marlow, OH, US<br>
          Riverton, OH, US
        </span>
      </li>
    </ul>
  </section>

</main>
</body>
</html>
```